Brookvane Consulting Business Card Design

Business Card Design for Brookvane Consulting. Brookvane Consulting is a boutique consultancy based in Atlanta, GA., that specializes in marketing strategy, organization planning, and leadership development. We provide solutions for small businesses and startups as well as Vantage 300 companies.

http://brookvaneconsulting.com/

Target Market(s)

We provide solutions for small businesses and startups as well as Vantage 300 companies.

Industry/Entity Type

Consulting

Contact Information for Business Card

Two sided business card with priority on contact information, logo, tag line (Clear Plans, Bold Steps, Lasting Growth Ahead)

Colors

Designer to choose colors to be used in the design.

Requirements
Must have
• contact information, logo, tag line (Clear Plans, Bold Steps, Lasting Growth Ahead)
• Simple no over communication.
Nice to have
• I would like to see different placements of logo and creative use of both sides of the card
Should not have
• Do not put too much information on the card.

```html
<!DOCTYPE html>
<html lang="en">
<head>
<meta charset="utf-8">
<title>Brookvane Consulting Business Card</title>
<link href="https://fonts.googleapis.com/css2?family=Lato:wght@400;700&display=swap" rel="stylesheet">
<style>
  :root {
    --backdrop: #4a413b;
    --card: #111112;
    --ink: #f4f4f4;
    --ink-soft: #c9c9c9;
    --ink-muted: #9a9a9a;
  }
  * { margin: 0; padding: 0; box-sizing: border-box; }
  html, body { width: 1200px; height: 769px; overflow: hidden; }
  body {
    background: var(--backdrop);
    font-family: "Lato", sans-serif;
    position: relative;
  }
  .card {
    position: absolute;
    top: 236px;
    width: 520px;
    height: 297px;
    background: var(--card);
    border-radius: 3px;
    overflow: hidden;
  }
  .card--front { left: 50px; }
  .card--back { left: 630px; }

  .wordmark {
    display: flex;
    align-items: center;
    gap: 10px;
    color: var(--ink);
  }
  .wordmark__square {
    width: 14px; height: 14px;
    border: 2px solid var(--ink);
    flex: none;
  }
  .wordmark__name {
    font-weight: 700;
    font-size: 26px;
    letter-spacing: 0.5px;
    line-height: 1.1;
  }

  .card--front .wordmark {
    position: absolute;
    left: 40px;
    top: 96px;
    width: 170px;
    align-items: flex-start;
  }
  .card--front .wordmark__square { margin-top: 6px; }
  .card--front .wordmark__name { font-size: 24px; }

  .contact {
    position: absolute;
    right: 34px;
    top: 96px;
    width: 240px;
    text-align: right;
    color: var(--ink-soft);
    font-size: 13px;
    line-height: 1.45;
  }
  .contact__name {
    color: var(--ink-muted);
    font-weight: 700;
    font-size: 15px;
    letter-spacing: 0.5px;
    text-transform: uppercase;
  }
  .contact__title { margin-bottom: 4px; }
  .contact__line {
    display: flex;
    justify-content: flex-end;
    align-items: center;
    gap: 7px;
  }
  .contact__line svg { width: 11px; height: 11px; fill: var(--ink-soft); flex: none; }

  .card__pattern {
    position: absolute;
    inset: 0;
    background: linear-gradient(135deg, #1a1a1c 0%, #141415 50%, #1d1d1f 100%);
  }
  .card--back .wordmark {
    position: absolute;
    left: 0; right: 0;
    top: 108px;
    justify-content: center;
  }
  .tagline {
    position: absolute;
    left: 0; right: 0;
    top: 196px;
    text-align: center;
    color: var(--ink-soft);
    font-size: 12px;
    letter-spacing: 0.3px;
  }
</style>
</head>
<body>
  <section class="card card--front" aria-label="Card front with contact details">
    <div class="wordmark">
      <span class="wordmark__square"></span>
      <span class="wordmark__name">Brookvane Consulting</span>
    </div>
    <div class="contact">
      <p class="contact__name">Darius Whitfield</p>
      <p class="contact__title">Founder/Managing Director</p>
      <p class="contact__line">404-555-0172
        <svg viewBox="0 0 24 24"><path d="M6.6 10.8a15 15 0 0 0 6.6 6.6l2.2-2.2a1 1 0 0 1 1-.25 11.4 11.4 0 0 0 3.6.57 1 1 0 0 1 1 1V20a1 1 0 0 1-1 1A17 17 0 0 1 3 4a1 1 0 0 1 1-1h3.5a1 1 0 0 1 1 1c0 1.25.2 2.450.57 3.57a1 1 0 0 1-.25 1z"/></svg>
      </p>
      <p class="contact__line">darius@brookvaneconsulting.com
        <svg viewBox="0 0 24 24"><path d="M2 5h20v14H2zm2 2v.4l8 5 8-5V7z"/></svg>
      </p>
      <p class="contact__line">brookvaneconsulting.com
        <svg viewBox="0 0 24 24"><circle cx="12" cy="12" r="10"/></svg>
      </p>
    </div>
  </section>

  <section class="card card--back" aria-label="Card back with name and tagline">
    <div class="card__pattern" role="img" aria-label="Faint tonal pattern of small dark rectangles covering the card"></div>
    <div class="wordmark">
      <span class="wordmark__square"></span>
      <span class="wordmark__name">Brookvane Consulting</span>
    </div>
    <p class="tagline">Clear Plans, Bold Steps, Lasting Growth Ahead</p>
  </section>
</body>
</html>
```